Professional violinist needs business cards

I am trying to attract the following jobs:
-private violin lessons (primarily classical)
-performance gigs (weddings, birthday parties, funerals, etc.)
-collaborations with other artists (studio recordings, performances)

I want to communicate that I have a very high standard of excellence for my work, but I also love people and celebrations.
Values/style words I like are:
love, joy, peace, fun, beauty, authenticity, excellence, warmth, refined/sleek, free spirited. If that's too confusing, just ignore :)

I will attach my favorite business card template that I could find on Canva. The lines are supposed to be like a music staff, which I think is really cool, but I also don't want it to look too busy. I like the simple black and white--I think it looks sharp--but I also am open to other ideas. I also have seen business cards with pictures included that looked great, so I attached an image that could be used as well.

I am also attaching a file that I made of my initials that could be used as a logo, but I'm not sure if it should be included.

Information on the card:
-My name (18 letters total)
-"violinist"
-phone number, email, website

Thank you!

```html
<!DOCTYPE html>
<html lang="en">
<head>
<meta charset="utf-8">
<title>Caroline Westbrook — Violinist Business Card</title>
<link href="https://fonts.googleapis.com/css2?family=Barlow+Semi+Condensed:wght@400;600&family=Barlow:wght@500&display=swap" rel="stylesheet">
<style>
  :root {
    --canvas: #e4e2df;
    --card-white: #f7f7f7;
    --card-black: #000000;
    --ink: #141414;
    --ink-soft: #3a3a3a;
    --mark-grey: #6b6b6b;
    --photo-dark: #2b2b2b;
    --photo-mid: #8a8a8a;
    --photo-light: #d9d9d9;
  }
  * { box-sizing: border-box; margin: 0; padding: 0; }
  html, body {
    width: 1200px; height: 1200px; overflow: hidden;
    background: var(--canvas);
  }
  .stage {
    width: 1200px; height: 1200px;
    display: flex; flex-direction: column; align-items: center; justify-content: center;
    gap: 52px;
  }
  .card {
    position: relative;
    width: 900px; height: 514px;
    overflow: hidden;
    box-shadow: 0 6px 18px rgba(0,0,0,0.18);
  }
  .card-front { background: var(--card-white); }
  .card-back  { background: var(--card-black); display: flex; align-items: center; justify-content: center; }

  .portrait {
    position: absolute; top: 0; right: 0;
    width: 500px; height: 100%;
    background:
      radial-gradient(ellipse at 72% 30%, var(--photo-light) 0%, transparent 38%),
      linear-gradient(100deg, var(--photo-light) 0%, var(--photo-mid) 30%, var(--photo-dark) 62%, #1a1a1a 100%);
    clip-path: polygon(22% 0, 100% 0, 100% 100%, 44% 100%, 38% 90%, 32% 80%, 28% 66%, 20% 56%, 24% 44%, 14% 34%, 18% 22%, 12% 12%);
  }

  .identity { position: absolute; left: 92px; top: 150px; }
  .name {
    font-family: "Barlow Semi Condensed", sans-serif;
    font-size: 38px; line-height: 1; color: var(--ink);
    text-transform: uppercase; letter-spacing: 0.01em;
  }
  .name .first { font-weight: 600; }
  .name .last { font-weight: 400; }
  .role {
    margin-top: 10px;
    font-family: "Barlow Semi Condensed", sans-serif;
    font-size: 18px; letter-spacing: 0.32em; color: var(--ink-soft);
    text-transform: uppercase;
  }

  .contacts { position: absolute; left: 92px; top: 300px; list-style: none; }
  .contact {
    display: flex; align-items: center; gap: 22px;
    height: 54px;
    font-family: "Barlow", sans-serif; font-weight: 500;
    font-size: 24px; color: var(--ink);
  }
  .contact svg { width: 28px; height: 28px; flex: none; fill: var(--ink); }

  .back-name {
    font-family: "Barlow Semi Condensed", sans-serif; font-weight: 400;
    font-size: 56px; color: var(--mark-grey); letter-spacing: 0.02em;
  }
</style>
</head>
<body>
<main class="stage">
  <section class="card card-front">
    <div class="portrait" role="img" aria-label="Black and white portrait photograph of the violinist holding her violin against a brick wall"></div>
    <div class="identity">
      <h1 class="name"><span class="first">Caroline</span> <span class="last">Westbrook</span></h1>
      <p class="role">Violinist</p>
    </div>
    <ul class="contacts">
      <li class="contact">
        <svg viewBox="0 0 24 24" aria-hidden="true"><path d="M6.6 10.8a15.1 15.1 0 0 0 6.6 6.6l2.2-2.2a1 1 0 0 1 1-.25 11.4 11.4 0 0 0 3.6.57 1 1 0 0 1 1 1V20a1 1 0 0 1-1 1A17 17 0 0 1 3 4a1 1 0 0 1 1-1h3.5a1 1 0 0 1 1 1c0 1.25.2 2.45.57 3.6a1 1 0 0 1-.25 1z"/></svg>
        <span>(555) 218 - 4630</span>
      </li>
      <li class="contact">
        <svg viewBox="0 0 24 24" aria-hidden="true"><path d="M2 5h20v14H2z M4 7v.3l8 5.2 8-5.2V7z M4 9.6V17h16V9.6l-8 5.2z" fill-rule="evenodd"/></svg>
        <span>carolinewestbrook@mailbox.com</span>
      </li>
      <li class="contact">
        <svg viewBox="0 0 24 24" aria-hidden="true"><path d="M12 2a10 10 0 1 0 0 20 10 10 0 0 0 0-20zm0 1.8c1.2 1.3 2.1 3.4 2.4 6.2H9.6c.3-2.8 1.2-4.9 2.4-6.2zM8 10H3.9A8.2 8.2 0 0 1 9.4 4.2 12.4 12.4 0 0 0 8 10zm0 2c.1 2.4.7 4.4 1.4 5.8A8.2 8.2 0 0 1 3.9 12zm1.6 0h4.8c-.3 2.8-1.2 4.9-2.4 6.2-1.2-1.3-2.1-3.4-2.4-6.2zm6.4 0h4.1a8.2 8.2 0 0 1-5.5 5.8c.7-1.4 1.3-3.4 1.4-5.8zm0-2a12.4 12.4 0 0 0-1.4-5.8A8.2 8.2 0 0 1 20.1 10z"/></svg>
        <span>www.carolinewestbrook.com</span>
      </li>
    </ul>
  </section>

  <section class="card card-back">
    <p class="back-name">Caroline Westbrook</p>
  </section>
</main>
</body>
</html>
```